Cafe - A FRAME Design

Need to create an A frame for my café.
Logo available
Word document - has basic information we think would be good.

Name: Wuzzop Café

Notes from the A-frame printers.
File Requirements
• PDF without trim, crop or registration marks
• All files to be CMYK, not RGB
• All fonts converted to outlines (paths/curves)
• Embed all images and elements
• Files to be 100% scale unless otherwise specified
• 10mm Bleed
Resolution
• Bitmap images no less than 130 DPI at full size
Pantone Colours
• If required Pantone colours must be supplied

Target Market(s)

Mainly Students - University cafe

Requirements
Must have
• Cafe name: Wuzzop
Nice to have
• Might be nice to have background - that orange color same as logo - just an idea

Word document - has basic idea regarding text that should be included

```html
<!DOCTYPE html>
<html lang="en">
<head>
<meta charset="utf-8">
<title>Wuzzop Café – A-Frame</title>
<link href="https://fonts.googleapis.com/css2?family=Poppins:wght@300;400;600;700;800&family=Yellowtail&display=swap" rel="stylesheet">
<style>
  :root {
    --page-bg: #e6e2dc;
    --poster-bg: #f6f6f6;
    --orange: #ec6a2c;
    --brown: #5b2a1b;
    --bean-dark: #3a1d10;
    --bean-mid: #7a4325;
    --ink: #1c1a19;
    --white: #ffffff;
  }
  * { box-sizing: border-box; margin: 0; padding: 0; }
  html, body { width: 1054px; height: 1200px; overflow: hidden; }
  body {
    background: var(--page-bg);
    font-family: "Poppins", sans-serif;
    position: relative;
  }
  .poster {
    position: absolute;
    left: 197px; top: 20px;
    width: 660px; height: 1160px;
    background: var(--poster-bg);
    overflow: hidden;
    box-shadow: 0 6px 24px rgba(0,0,0,.18);
  }
  .beans {
    position: absolute; left: 0; width: 100%;
  }
  .beans--top {
    top: 0; height: 150px;
    background: linear-gradient(180deg, var(--bean-dark) 0%, var(--bean-mid) 45%, rgba(122,67,37,0) 100%);
  }
  .beans--bottom {
    bottom: 0; height: 170px;
    background: linear-gradient(0deg, var(--bean-dark) 0%, var(--bean-mid) 60%, rgba(122,67,37,0) 100%);
  }
  .brand {
    position: absolute; top: 148px; left: 0; width: 100%;
    display: flex; justify-content: center; align-items: center; gap: 16px;
  }
  .brand__mark {
    width: 50px; height: 50px; border-radius: 50%;
    border: 4px solid var(--orange);
  }
  .brand__text { display: flex; flex-direction: column; align-items: flex-end; }
  .brand__name {
    font-weight: 600; font-size: 46px; line-height: 1; color: var(--ink);
  }
  .brand__sub {
    font-weight: 400; font-size: 14px; letter-spacing: 6px; color: var(--ink);
    text-transform: uppercase; margin-top: 4px;
  }
  .tagline {
    position: absolute; top: 262px; left: 0; width: 100%;
    text-align: center; font-weight: 800; font-size: 23px; line-height: 1.3;
    color: var(--ink); text-transform: uppercase;
  }
  .divider {
    position: absolute; top: 364px; left: 295px;
    width: 70px; height: 5px; background: var(--brown);
  }
  .headline__script {
    position: absolute; top: 368px; left: 0; width: 100%;
    text-align: center; font-family: "Yellowtail", cursive;
    font-size: 108px; line-height: 1; color: var(--orange);
    white-space: nowrap; transform: rotate(-4deg);
    z-index: 2;
  }
  .headline__main {
    position: absolute; top: 478px; left: 0; width: 100%;
    text-align: center; font-weight: 800; font-size: 136px; line-height: 1;
    color: var(--brown); letter-spacing: -4px;
  }
  .offer-list {
    position: absolute; top: 662px; left: 80px; right: 70px;
    display: flex; justify-content: space-between; list-style: none;
  }
  .offer {
    display: flex; flex-direction: column; align-items: center; gap: 14px;
    position: relative;
  }
  .offer + .offer::before {
    content: ""; position: absolute; left: -30px; top: 0;
    width: 2px; height: 88px; background: var(--orange);
  }
  .offer__icon { width: 76px; height: 76px; }
  .offer__label {
    font-weight: 700; font-size: 26px; color: var(--ink); text-transform: uppercase;
    letter-spacing: -.5px;
  }
  .notice {
    position: absolute; top: 812px; left: 66px; width: 534px; height: 86px;
    background: var(--orange); color: var(--white);
    display: flex; flex-direction: column; justify-content: center; align-items: center;
    text-transform: uppercase; line-height: 1.2;
  }
  .notice__dietary { font-weight: 300; font-size: 26px; }
  .notice__catering { font-weight: 700; font-size: 26px; }
  .location {
    position: absolute; top: 940px; left: 0; width: 100%;
    display: flex; justify-content: center; align-items: center; gap: 12px;
    font-weight: 700; font-size: 27px; color: var(--brown); text-transform: uppercase;
  }
  .location__pin { width: 24px; height: 34px; }
</style>
</head>
<body>
  <main class="poster">
    <div class="beans beans--top" role="img" aria-label="Scattered roasted coffee beans along the top edge"></div>

    <header class="brand">
      <span class="brand__mark"></span>
      <span class="brand__text">
        <span class="brand__name">wuzzop</span>
        <span class="brand__sub">Catering</span>
      </span>
    </header>

    <p class="tagline">Your environmentally &amp;<br>sustainability focused café</p>

    <span class="divider"></span>

    <h1 class="headline">
      <span class="headline__main">Coffee</span>
      <span class="headline__script">Specialty</span>
    </h1>

    <ul class="offer-list">
      <li class="offer">
        <svg class="offer__icon" viewBox="0 0 76 76" fill="none" stroke="#ec6a2c" stroke-width="3">
          <circle cx="38" cy="38" r="35"/>
          <path d="M22 36 q10-12 20 0 z M22 40 h20 M22 44 h20 q0 6-10 6 q-10 0-10-6" stroke-linejoin="round"/>
          <path d="M46 34 h10 l-2 18 h-6 z M48 34 v-6 M52 34 v-8"/>
        </svg>
        <span class="offer__label">Fresh Food</span>
      </li>
      <li class="offer">
        <svg class="offer__icon" viewBox="0 0 76 76" fill="none" stroke="#ec6a2c" stroke-width="3">
          <circle cx="38" cy="38" r="35"/>
          <path d="M26 38 q-2-10 8-10 q4-8 8 0 q10 0 8 10 z" stroke-linejoin="round"/>
          <path d="M26 40 h24 l-4 14 h-16 z M34 40 v14 M42 40 v14"/>
        </svg>
        <span class="offer__label">Pastries</span>
      </li>
      <li class="offer">
        <svg class="offer__icon" viewBox="0 0 76 76" fill="none" stroke="#ec6a2c" stroke-width="3">
          <circle cx="38" cy="38" r="35"/>
          <path d="M28 28 h20 M29 28 l3 28 h12 l3-28 M40 28 l4-10 M31 36 h14"/>
          <circle cx="36" cy="44" r="2"/><circle cx="41" cy="49" r="2"/>
        </svg>
        <span class="offer__label">Drinks</span>
      </li>
    </ul>

    <div class="notice">
      <span class="notice__dietary">(Vegan &amp; GF) options available</span>
      <span class="notice__catering">Catering available</span>
    </div>

    <p class="location">
      <svg class="location__pin" viewBox="0 0 24 34">
        <path d="M12 0 C5 0 0 5 0 12 C0 20 12 34 12 34 C12 34 24 20 24 12 C24 5 19 0 12 0 Z" fill="#ec6a2c"/>
        <circle cx="12" cy="12" r="4.5" fill="#f6f6f6"/>
      </svg>
      <span>Located @ Building 418</span>
    </p>

    <div class="beans beans--bottom" role="img" aria-label="Pile of roasted coffee beans along the bottom edge"></div>
  </main>
</body>
</html>
```